Two Separate Canvas Posters 54"width x 36" Height

I need two (2) posters designed for a new restaurant concept called: Lumara Fresh Pita Grill.
Both posters will be printed on Canvas and placed into our new restaurants dining area.
I want this to look hip and cool.
I want so see red colors and earth tones. Please see attached for some ideas that I have.
The final design should communicate that you really gotta have this product and that this is a fun and casual place for a quick bite on the go.
Poster 1 message: gotta Eatta pita!
Size: 54"width x 36" high
Idea: Please see attached for design ideas and colors that I would like to see. If you can come up with any better idea, I would love to see this.
Poster 2 message: Power to the Pita
Size: 54"width x 36" height
Idea: Please see attached for design idea and colors that I want to see.
Industry/Entity Type
Restaurant
Look and feel
Each slider illustrates characteristics of the customer's brand and the style your logo design should communicate.

```html
<!DOCTYPE html>
<html lang="en">
<head>
<meta charset="utf-8">
<title>Power to the Pita – Lumara Fresh Pita Grill</title>
<link rel="stylesheet" href="https://fonts.googleapis.com/css2?family=Didact+Gothic&family=Poppins:wght@700&display=swap">
<style>
  :root {
    --page: #ffffff;
    --green: #1f9a3e;
    --red: #e3262b;
    --cream-text: rgba(255, 242, 228, 0.78);
    --tag-bg: rgba(255, 246, 238, 0.82);
    --s1: #d8262a;
    --s2: #e8432a;
    --s3: #f07a2c;
    --s4: #f49a3a;
    --s5: #f7b45a;
    --s6: #fbd69a;
    --s7: #c9302a;
    --s8: #a8281f;
  }
  html, body {
    margin: 0;
    padding: 0;
    overflow: hidden;
    background: var(--page);
  }
  .canvas {
    position: relative;
    width: 1200px;
    height: 887px;
    background: var(--page);
    overflow: hidden;
  }
  .poster {
    position: absolute;
    left: 18px;
    top: 61px;
    width: 1163px;
    height: 775px;
    background: linear-gradient(90deg,
      var(--s1) 0%, var(--s1) 2%, var(--s2) 2%, var(--s2) 4%,
      var(--s3) 4%, var(--s3) 5.5%, var(--s1) 5.5%, var(--s1) 8%,
      var(--s2) 8%, var(--s2) 10%, var(--s4) 10%, var(--s4) 11%,
      var(--s7) 11%, var(--s7) 14%, var(--s2) 14%, var(--s2) 16%,
      var(--s3) 16%, var(--s3) 18%, var(--s1) 18%, var(--s1) 20%,
      var(--s4) 20%, var(--s4) 22%, var(--s3) 22%, var(--s3) 24%,
      var(--s2) 24%, var(--s2) 26%, var(--s4) 26%, var(--s4) 29%,
      var(--s5) 29%, var(--s5) 31%, var(--s3) 31%, var(--s3) 33%,
      var(--s5) 33%, var(--s5) 36%, var(--s6) 36%, var(--s6) 38%,
      var(--s5) 38%, var(--s5) 40%, var(--s4) 40%, var(--s4) 42%,
      var(--s6) 42%, var(--s6) 44%, var(--s5) 44%, var(--s5) 46%,
      var(--s4) 46%, var(--s4) 48%, var(--s6) 48%, var(--s6) 50%,
      var(--s5) 50%, var(--s5) 52%, var(--s3) 52%, var(--s3) 55%,
      var(--s4) 55%, var(--s4) 57%, var(--s2) 57%, var(--s2) 59%,
      var(--s3) 59%, var(--s3) 61%, var(--s8) 61%, var(--s8) 63%,
      var(--s2) 63%, var(--s2) 65%, var(--s3) 65%, var(--s3) 67%,
      var(--s1) 67%, var(--s1) 69%, var(--s4) 69%, var(--s4) 71%,
      var(--s2) 71%, var(--s2) 73%, var(--s3) 73%, var(--s3) 75%,
      var(--s7) 75%, var(--s7) 77%, var(--s4) 77%, var(--s4) 79%,
      var(--s2) 79%, var(--s2) 81%, var(--s3) 81%, var(--s3) 83%,
      var(--s1) 83%, var(--s1) 85%, var(--s3) 85%, var(--s3) 87%,
      var(--s2) 87%, var(--s2) 89%, var(--s8) 89%, var(--s8) 91%,
      var(--s3) 91%, var(--s3) 93%, var(--s7) 93%, var(--s7) 95%,
      var(--s2) 95%, var(--s2) 97%, var(--s8) 97%, var(--s8) 100%);
    overflow: hidden;
  }
  .artwork {
    position: absolute;
    inset: 0;
    width: 100%;
    height: 100%;
  }
  .headline-light {
    font-family: "Didact Gothic", "Century Gothic", sans-serif;
    fill: var(--cream-text);
  }
  .headline-bold {
    font-family: "Poppins", sans-serif;
    font-weight: 700;
  }
  .letter-green { fill: var(--green); }
  .letter-red { fill: var(--red); }
  .swoosh {
    fill: none;
    stroke: var(--green);
    stroke-width: 15;
    stroke-linecap: round;
  }
  .arrowhead { fill: var(--green); }
  .brand-tag { fill: var(--tag-bg); }
  .brand-name {
    font-family: "Poppins", sans-serif;
    font-weight: 700;
    fill: var(--green);
  }
</style>
</head>
<body>
<main class="canvas">
  <section class="poster" aria-label="Power to the Pita poster">
    <svg class="artwork" viewBox="0 0 1163 775" xmlns="http://www.w3.org/2000/svg">
      <!-- circular swoosh around the opening letters -->
      <path class="swoosh" d="M258 225 A112 112 0 1 1 452 252"/>
      <polygon class="arrowhead" points="432,262 468,236 470,282"/>

      <!-- headline -->
      <text class="headline-bold letter-green" x="248" y="283" font-size="220">p</text>
      <text class="headline-bold letter-red" x="382" y="283" font-size="190">o</text>
      <text class="headline-light" x="528" y="281" font-size="215" textLength="318" lengthAdjust="spacingAndGlyphs">wer</text>
      <text class="headline-light" x="552" y="474" font-size="180" textLength="455" lengthAdjust="spacingAndGlyphs">to the</text>
      <text class="headline-light" x="662" y="650" font-size="185" textLength="330" lengthAdjust="spacingAndGlyphs">pita</text>

      <!-- swooshes under the last line -->
      <path class="swoosh" d="M508 650 Q560 745 748 682"/>
      <polygon class="arrowhead" points="736,664 778,672 744,700"/>
      <path class="swoosh" d="M1088 650 Q1040 760 862 688"/>
      <polygon class="arrowhead" points="874,670 834,676 866,704"/>

      <!-- brand tag -->
      <rect class="brand-tag" x="0" y="563" width="286" height="105"/>
      <text class="brand-name" x="143" y="633" font-size="54" text-anchor="middle">Lumara</text>
    </svg>
  </section>
</main>
</body>
</html>
```